UX Design for Analytics Web Application

http://velqoranthe.com/
We are tech & consulting company with analytics products (web applications), located at Rio de Janeiro, Brazil.

We are searching a partner do develop UX for our products, i.e, aesthetics, usability, HTML/CSS.

Currently we have a product suite and the goal is to make a pilot re-design project with one of our products.

The product of interest is interactive webapp that aims at data analysis, significantly different from blogs, e-commerce or landing pages.

We do have a software development team but we lack an UX & HTML expert. Currently we use Bootstrap templates but the results are insatisfatory.

So, the project scope is, to develop the arts (UX, aesthetics, etc) along with the code/mockup (HTML/CSS) for one of our product (3 pages).

This is a pilot project and there's potential to rehire for our other products. Code quality is of importance.

More details and specification can be found in attached files.

Target Market(s)

Executives, managers & consultants

Industry/Entity Type

It Company

Coding

Coded - Design and coding required

Number of Pages Required

3 page

Font styles to use
Sans Serif

Requirements
Must have
• (see attached files, prefer the pptx version))
• -Responsive
Nice to have
• (see attached files, prefer the pptx version)
Should not have
• -Avoid Green, Red and Yellow colors. They have a meaning of good, bad and average in our products.

```html
<!DOCTYPE html>
<html lang="en">
<head>
<meta charset="utf-8">
<title>Velqoranthe – Processes Dashboard</title>
<link href="https://fonts.googleapis.com/css2?family=Open+Sans:wght@400;600;700;800&display=swap" rel="stylesheet">
<style>
  :root{
    --page-bg:#eeeeee;
    --surface:#ffffff;
    --ink:#3a3a3a;
    --muted:#8d8d8d;
    --line:#e2e2e2;
    --accent-primary:#2f6db5;
    --accent-price:#6a4fb3;
    --ring-one:#2f6db5;
    --ring-two:#6a4fb3;
    --ring-three:#3aa0d8;
    --ring-four:#4a4a4a;
    --new-bg:#dbe6f3;
    --footer-bg:#3d3d3d;
    --footer-ink:#bdbdbd;
  }
  *{box-sizing:border-box;margin:0;padding:0}
  html,body{width:820px;height:1200px;overflow:hidden}
  body{background:var(--page-bg);font-family:"Open Sans",Arial,sans-serif;color:var(--ink);position:relative}

  .app-header{height:58px;background:var(--surface);display:flex;align-items:center;justify-content:space-between;padding:0 24px;border-top:3px solid var(--accent-primary);box-shadow:0 1px 2px rgba(0,0,0,.06)}
  .brand{display:flex;align-items:center;gap:8px}
  .brand-dot{width:16px;height:16px;border-radius:50%;background:var(--accent-primary)}
  .brand-name{font-weight:700;font-size:18px;letter-spacing:1px;color:var(--ink)}
  .header-tools{display:flex;gap:14px}
  .header-tools svg{width:14px;height:14px;fill:var(--ink)}

  .section-title{text-align:center;font-weight:700;font-size:20px;letter-spacing:.5px;color:var(--ink)}
  .overview-title{margin-top:30px}
  .stats{display:flex;justify-content:center;gap:42px;margin-top:22px}
  .stat{width:108px;height:108px;border-radius:50%;border:8px solid;background:var(--surface);display:flex;flex-direction:column;align-items:center;justify-content:center;text-align:center;padding-top:4px}
  .stat--one{border-color:var(--ring-one)}
  .stat--two{border-color:var(--ring-two)}
  .stat--three{border-color:var(--ring-three)}
  .stat--four{border-color:var(--ring-four)}
  .stat-value{font-weight:700;font-size:24px;line-height:1.1}
  .stat-label{font-size:7px;font-weight:600;color:var(--muted);text-transform:uppercase;margin-top:3px;line-height:1.2;width:70px;height:17px}

  .feed-title{margin-top:40px}
  .content{width:636px;margin:0 auto}
  .feed{display:grid;grid-template-columns:repeat(3,1fr);gap:12px;margin-top:20px}
  .feed-card{background:var(--surface);height:122px;padding:16px 14px;display:flex;flex-direction:column}
  .feed-text{font-size:8.5px;line-height:1.55;color:var(--muted)}
  .feed-author{margin-top:auto;font-size:8.5px;font-weight:700;color:var(--accent-primary)}
  .feed-date{font-size:8px;color:var(--muted);margin-top:2px}

  .processes{display:grid;grid-template-columns:repeat(3,1fr);gap:12px;margin-top:22px}
  .process-card{background:var(--surface);height:115px;padding:16px 14px;display:flex;flex-direction:column}
  .process-head{display:flex;justify-content:space-between;font-weight:700;font-size:10px}
  .process-name{color:var(--accent-primary)}
  .process-price{color:var(--accent-price)}
  .process-text{font-size:8.5px;line-height:1.55;color:var(--muted);margin-top:8px}
  .process-step{margin-top:auto;font-size:7px;font-weight:700;color:var(--accent-primary);text-transform:uppercase}
  .new-process{background:var(--new-bg);height:115px;display:flex;align-items:center;justify-content:center;font-weight:700;font-size:17px;color:var(--ink)}

  .app-footer{position:absolute;left:0;right:0;bottom:0;height:42px;background:var(--footer-bg);color:var(--footer-ink);font-size:8px;display:flex;align-items:center;justify-content:center}
</style>
</head>
<body>
<header class="app-header">
  <div class="brand"><span class="brand-dot"></span><span class="brand-name">VELQORANTHE</span></div>
  <nav class="header-tools" aria-label="Account tools">
    <svg viewBox="0 0 16 16" aria-label="Notifications"><path d="M8 1a4 4 0 0 0-4 4v4L2 12h12l-2-3V5a4 4 0 0 0-4-4zm-2 12a2 2 0 0 0 4 0z"/></svg>
    <svg viewBox="0 0 16 16" aria-label="Profile"><circle cx="8" cy="5" r="3.2"/><path d="M2 15c0-3.5 2.7-5.5 6-5.5s6 2 6 5.5z"/></svg>
    <svg viewBox="0 0 16 16" aria-label="Settings"><path d="M7 0h2l.4 2.2 1.6.7 1.9-1.3 1.4 1.4-1.3 1.9.7 1.6L16 7v2l-2.2.4-.7 1.6 1.3 1.9-1.4 1.4-1.9-1.3-1.6.7L9 16H7l-.4-2.2-1.6-.7-1.9 1.3-1.4-1.4 1.3-1.9-.7-1.6L0 9V7l2.2-.4.7-1.6L1.6 3.1 3 1.7l1.9 1.3 1.6-.7zM8 5.5a2.5 2.5 0 1 0 0 5 2.5 2.5 0 0 0 0-5z"/></svg>
  </nav>
</header>

<main>
  <h2 class="section-title overview-title">PROCESSES OVERVIEW</h2>
  <div class="stats">
    <div class="stat stat--one"><span class="stat-value">72</span><span class="stat-label">Active processes</span></div>
    <div class="stat stat--two"><span class="stat-value">28</span><span class="stat-label">Completed processes</span></div>
    <div class="stat stat--three"><span class="stat-value">$5000</span><span class="stat-label">Total earned</span></div>
    <div class="stat stat--four"><span class="stat-value">72%</span><span class="stat-label">Completed</span></div>
  </div>

  <h2 class="section-title feed-title">ACTIVITY FEED</h2>
  <div class="content">
    <section class="feed">
      <article class="feed-card"><p class="feed-text">Lorem ipsum dolor sit amet, consectetur adipiscing elit, sed do eiusmod tempor incididunt ut labore et dolore magna.</p><p class="feed-author">JOHN DOE</p><p class="feed-date">21 MAR 2017</p></article>
      <article class="feed-card"><p class="feed-text">Lorem ipsum dolor sit amet, consectetur adipiscing elit, sed do eiusmod tempor incididunt ut labore et dolore magna.</p><p class="feed-author">JOHN DOE</p><p class="feed-date">21 MAR 2017</p></article>
      <article class="feed-card"><p class="feed-text">Lorem ipsum dolor sit amet, consectetur adipiscing elit, sed do eiusmod tempor incididunt ut labore et dolore magna.</p><p class="feed-author">JOHN DOE</p><p class="feed-date">21 MAR 2017</p></article>
    </section>

    <section class="processes">
      <article class="process-card"><div class="process-head"><span class="process-name">PROCESS NAME</span><span class="process-price">$150</span></div><p class="process-text">Lorem ipsum dolor sit amet consectetur adipiscing elit sed do eiusmod tempor.</p><p class="process-step">Current step: execution negotiation</p></article>
      <article class="process-card"><div class="process-head"><span class="process-name">PROCESS NAME</span><span class="process-price">$150</span></div><p class="process-text">Lorem ipsum dolor sit amet consectetur adipiscing elit sed do eiusmod tempor.</p><p class="process-step">Current step: execution negotiation</p></article>
      <article class="process-card"><div class="process-head"><span class="process-name">PROCESS NAME</span><span class="process-price">$150</span></div><p class="process-text">Lorem ipsum dolor sit amet consectetur adipiscing elit sed do eiusmod tempor.</p><p class="process-step">Current step: execution negotiation</p></article>
      <article class="process-card"><div class="process-head"><span class="process-name">PROCESS NAME</span><span class="process-price">$150</span></div><p class="process-text">Lorem ipsum dolor sit amet consectetur adipiscing elit sed do eiusmod tempor.</p><p class="process-step">Current step: execution negotiation</p></article>
      <article class="process-card"><div class="process-head"><span class="process-name">PROCESS NAME</span><span class="process-price">$150</span></div><p class="process-text">Lorem ipsum dolor sit amet consectetur adipiscing elit sed do eiusmod tempor.</p><p class="process-step">Current step: execution negotiation</p></article>
      <article class="process-card"><div class="process-head"><span class="process-name">PROCESS NAME</span><span class="process-price">$150</span></div><p class="process-text">Lorem ipsum dolor sit amet consectetur adipiscing elit sed do eiusmod tempor.</p><p class="process-step">Current step: execution negotiation</p></article>
      <article class="process-card"><div class="process-head"><span class="process-name">PROCESS NAME</span><span class="process-price">$150</span></div><p class="process-text">Lorem ipsum dolor sit amet consectetur adipiscing elit sed do eiusmod tempor.</p><p class="process-step">Current step: execution negotiation</p></article>
      <article class="process-card"><div class="process-head"><span class="process-name">PROCESS NAME</span><span class="process-price">$150</span></div><p class="process-text">Lorem ipsum dolor sit amet consectetur adipiscing elit sed do eiusmod tempor.</p><p class="process-step">Current step: execution negotiation</p></article>
      <article class="process-card"><div class="process-head"><span class="process-name">PROCESS NAME</span><span class="process-price">$150</span></div><p class="process-text">Lorem ipsum dolor sit amet consectetur adipiscing elit sed do eiusmod tempor.</p><p class="process-step">Current step: execution negotiation</p></article>
      <article class="process-card"><div class="process-head"><span class="process-name">PROCESS NAME</span><span class="process-price">$150</span></div><p class="process-text">Lorem ipsum dolor sit amet consectetur adipiscing elit sed do eiusmod tempor.</p><p class="process-step">Current step: execution negotiation</p></article>
      <article class="process-card"><div class="process-head"><span class="process-name">PROCESS NAME</span><span class="process-price">$150</span></div><p class="process-text">Lorem ipsum dolor sit amet consectetur adipiscing elit sed do eiusmod tempor.</p><p class="process-step">Current step: execution negotiation</p></article>
      <article class="process-card"><div class="process-head"><span class="process-name">PROCESS NAME</span><span class="process-price">$150</span></div><p class="process-text">Lorem ipsum dolor sit amet consectetur adipiscing elit sed do eiusmod tempor.</p><p class="process-step">Current step: execution negotiation</p></article>
      <article class="process-card"><div class="process-head"><span class="process-name">PROCESS NAME</span><span class="process-price">$150</span></div><p class="process-text">Lorem ipsum dolor sit amet consectetur adipiscing elit sed do eiusmod tempor.</p><p class="process-step">Current step: execution negotiation</p></article>
      <a class="new-process">+ NEW PROCESS</a>
    </section>
  </div>
</main>

<footer class="app-footer">© 2017 Velqoranthe.com. All Rights Reserved</footer>
</body>
</html>
```